Design a Website in Wordpress for an Australian Health Training Company in Health related courses

We require a WORDPRESS based Website (due to add on's we need to use for third party software) to replace our old site.
We offer national face to face delivery in medical reception, terminology and also administration.
The website will have around 6 pages and the ability to describe our main 6 courses (perhaps on the Courses page this may be tabs opening up to details for example?)
I have attached a previous sample of a Joomla site which was being developed (please do not feel you have to copy this - but I am just giving it as a sample - copying would be boring). But it gives an idea of look/feel and colours which may be suitable. Open to other ideas though.
I will provide some of the content, but would like the ability to finish the content myself.
Images and graphics are important. While a few medical photos re great - don't be tempted to us all pictures of doctors and nurses (although a couple would be good) - these are administrative courses so general corporate, eye catching visionary pictures of people in general are great. A medical type picture is also fine.
THE BOOKING system - will be via an ADD ON which will occur at the end of the project and is supplied by a third party software company (our student management system). This project will include up to 2 hours working with the Tech guys from the third party software to enable the ADD ON. If this ADD ON requires more time, we will pay hourly (although I do not expect it will).
Target Market(s)
Mostly a female market, many mature aged women target 25-45 yrs. Mixture of medical/health and corporate. Maybe a bit of mums returning to work and corporate inspiration.
Industry/Entity Type
It Company
Coding
Coded - Design and coding required
Number of Pages Required
5+ page
Requirements
Must have
- Wordpress
- Great graphics
- Interesting
- professional and clean
- Enquiry section (info Pak)
- Should have a University feel to it - Education
- Pages
- Home Page - About Us - Recruitment -Courses - Class Schedule - Traineeships Queensland Funding - Latest News Blog - Corporate Training- Contact us

```html
<!DOCTYPE html>
<html lang="en">
<head>
<meta charset="utf-8">
<title>Harbourline Institute of Training</title>
<link href="https://fonts.googleapis.com/css2?family=Raleway:wght@400;500;600;700&family=Open+Sans:wght@400;600;700&display=swap" rel="stylesheet">
<style>
:root{
  --blue:#0a5bc4;
  --blue-dark:#0747a0;
  --blue-band:#0c55bd;
  --orange:#f39a2c;
  --ink:#333333;
  --muted:#555555;
  --link:#1a5fb4;
  --footer:#333333;
  --footer-bar:#252525;
  --white:#ffffff;
}
*{box-sizing:border-box;margin:0;padding:0}
html,body{width:1200px;height:2671px;overflow:hidden}
body{font-family:"Open Sans",sans-serif;color:var(--ink);background:var(--white);position:relative}
.section{position:absolute;left:0;width:1200px}
.abs{position:absolute}

/* header */
.site-header{top:0;height:164px;background:var(--white)}
.brand{left:142px;top:40px;width:160px;display:flex;align-items:center;gap:10px}
.brand-mark{width:18px;height:18px;border-radius:50%;background:var(--blue-dark);flex:none}
.brand-name{font-family:"Raleway",sans-serif;font-weight:700;font-size:17px;line-height:1.2;color:var(--blue-dark);text-transform:uppercase}
.search{left:484px;top:80px;width:228px;height:32px;border:1px solid #cfcfcf;display:flex}
.search span{flex:1;font-size:12px;color:#999;padding:8px 10px}
.search button{width:34px;border:0;background:var(--blue-dark);display:flex;align-items:center;justify-content:center}
.phone{left:750px;top:80px;display:flex;align-items:center;gap:14px;font-size:16px;color:#444}
.phone-dot{width:30px;height:30px;border-radius:50%;background:var(--orange);display:flex;align-items:center;justify-content:center}
.btn-top{left:960px;width:106px;height:31px;background:var(--blue-dark);color:var(--white);font-size:12px;font-weight:600;display:flex;align-items:center;justify-content:center;letter-spacing:.5px;border-radius:2px}

/* nav */
.main-nav{top:164px;height:55px;background:linear-gradient(#1467d2,#0b55bd)}
.main-nav ul{list-style:none;display:flex;position:absolute;left:132px;top:0;height:55px}
.main-nav li{font-size:13px;color:var(--white);padding:0 18px;display:flex;align-items:center;border-right:1px solid rgba(255,255,255,.25)}
.main-nav li.active{background:var(--orange)}

/* hero */
.hero{top:219px;height:395px}
.hero-photo{left:0;top:0;width:1200px;height:395px;background:linear-gradient(100deg,#c9d6e1 0%,#eef2f5 30%,#dfe6ec 55%,#b9c7d3 100%)}
.hero-caption{left:130px;top:84px;width:326px;height:231px;background:rgba(255,255,255,.55);padding:26px 32px}
.hero-caption .kicker{font-family:"Raleway",sans-serif;font-size:20px;color:#333}
.hero-caption h1{font-family:"Raleway",sans-serif;font-weight:700;font-size:37px;color:var(--blue-dark);margin-top:2px}
.hero-caption p{font-size:12px;line-height:1.6;margin-top:10px;color:#333}
.hero-caption .btn{display:inline-block;margin-top:22px;background:var(--blue-dark);color:var(--white);font-size:12px;padding:10px 16px;border-radius:2px}
.arrow-round{width:30px;height:30px;border-radius:50%;background:rgba(60,60,60,.55);display:flex;align-items:center;justify-content:center}
.enquire{left:787px;top:0;width:278px;height:395px;background:rgba(150,160,170,.7);padding:18px 20px}
.enquire h2{font-family:"Raleway",sans-serif;font-weight:700;font-size:25px;color:var(--white);letter-spacing:.5px}
.enquire .field{height:36px;background:var(--white);border-radius:3px;margin-top:9px;font-size:12px;color:#777;padding:10px 12px}
.enquire .field:first-of-type{margin-top:12px}
.enquire .submit{margin-top:14px;height:44px;background:var(--blue-dark);color:var(--white);font-weight:700;font-size:15px;letter-spacing:1px;display:flex;align-items:center;justify-content:center;border-radius:3px}

/* courses band */
.courses{top:614px;height:280px;background:linear-gradient(#0f60c9,#0849a8)}
.course{top:30px;width:220px;text-align:center;color:var(--white)}
.course .icon{width:93px;height:93px;border-radius:50%;background:var(--white);margin:0 auto;display:flex;align-items:center;justify-content:center}
.course h3{font-family:"Raleway",sans-serif;font-weight:500;font-size:21px;line-height:1.2;margin-top:22px;height:52px}
.course p{font-size:12px;line-height:1.6;margin-top:14px}
.band-arrow{top:140px}

/* welcome */
.welcome{top:894px;height:267px;text-align:center}
.welcome h2{font-family:"Raleway",sans-serif;font-weight:500;font-size:33px;letter-spacing:1px;margin-top:40px;color:#222}
.welcome p{width:936px;margin:18px auto 0;font-size:11.5px;line-height:1.75;color:#333;text-align:center}
.btn-small{display:inline-block;background:var(--blue-dark);color:var(--white);font-size:11px;padding:7px 9px;border-radius:3px;margin-top:16px}

/* testimonials */
.testimonials{top:1161px;height:308px;text-align:center;color:var(--white)}
.testimonials .photo{left:0;top:0;width:1200px;height:308px;background:linear-gradient(100deg,#6d7a87 0%,#99a4ae 40%,#8a949e 70%,#6e7883 100%)}
.testimonials h2{position:relative;font-family:"Raleway",sans-serif;font-weight:500;font-size:31px;letter-spacing:1px;margin-top:44px}
.testimonials p{position:relative;width:1040px;margin:18px auto 0;font-size:11.5px;line-height:1.8}
.testimonials .who{position:relative;font-style:italic;font-size:12px;margin-top:18px}
.t-controls{position:relative;display:flex;justify-content:center;gap:8px;margin-top:20px}
.t-controls span{width:26px;height:26px;border:1px solid rgba(255,255,255,.8);display:flex;align-items:center;justify-content:center}

/* why */
.why{top:1469px;height:453px;border-bottom:1px solid #e2e2e2}
.why h2{font-family:"Raleway",sans-serif;font-weight:500;font-size:30px;letter-spacing:1px;text-align:center;margin-top:46px;color:#222}
.feature{width:430px;padding-left:44px}
.feature svg{position:absolute;left:0;top:4px}
.feature h3{font-family:"Raleway",sans-serif;font-weight:500;font-size:20px;color:var(--link);letter-spacing:.5px}
.feature p{font-size:11px;line-height:1.8;margin-top:8px;color:#444}

/* blog */
.blog{top:1922px;height:449px;background:linear-gradient(#ffffff 0%,#f3f3f3 40%,#e4e4e4 100%)}
.blog h2{font-family:"Raleway",sans-serif;font-weight:500;font-size:30px;letter-spacing:1px;text-align:center;margin-top:44px;color:#222}
.post{top:106px;width:284px}
.post .thumb{width:284px;height:164px;border:4px solid var(--white);box-shadow:0 1px 3px rgba(0,0,0,.2)}
.post h3{font-family:"Raleway",sans-serif;font-weight:500;font-size:15px;color:var(--link);margin-top:16px}
.post .date{font-size:11px;color:#333;margin-top:6px;padding-left:3px}
.post p{font-size:11px;line-height:1.7;color:#555;margin-top:12px}
.post .more{font-size:11px;font-weight:700;color:var(--blue-dark);margin-top:12px;display:flex;align-items:center;gap:6px}
.live-chat{left:913px;top:403px;width:152px;height:46px;background:var(--blue-dark);color:var(--white);font-size:15px;letter-spacing:1px;display:flex;align-items:center;justify-content:center;gap:10px}

/* footer */
.site-footer{top:2371px;height:239px;background:var(--footer);color:#eee}
.site-footer h4{font-family:"Raleway",sans-serif;font-weight:500;font-size:16px;letter-spacing:1px;color:var(--white)}
.f-brand{left:134px;top:30px;width:140px}
.f-brand .brand-name{color:#ddd;font-size:15px}
.socials{left:134px;top:178px;display:flex;gap:10px}
.socials span{width:26px;height:26px;border-radius:50%;background:#6a6a6a}
.socials span:first-child{background:var(--blue-dark)}
.f-links{left:344px;top:32px}
.f-links ul{list-style:none;margin-top:18px}
.f-links li{font-size:11px;line-height:19.5px}
.f-news{left:593px;top:32px;width:190px}
.f-news p{font-size:11px;line-height:1.7;margin-top:18px}
.f-news .input{margin-top:16px;height:34px;background:#4a4a4a;border-radius:3px;font-size:11px;padding:10px;letter-spacing:.5px}
.f-news .sub{margin-top:14px;display:inline-block;background:var(--blue-dark);font-size:11px;padding:8px 10px;border-radius:2px}
.f-contact{left:855px;top:32px;width:220px}
.f-contact ul{list-style:none;margin-top:18px}
.f-contact li{font-size:11px;line-height:1.5;display:flex;gap:14px;margin-bottom:12px}
.f-contact li svg{flex:none;margin-top:2px}
.f-contact a{color:#eee}
.copyright{top:2610px;height:61px;background:var(--footer-bar);color:#ccc;font-size:11px;display:flex;align-items:center;justify-content:center}
</style>
</head>
<body>

<header class="section site-header">
  <div class="abs brand">
    <span class="brand-mark"></span>
    <span class="brand-name">Harbourline Institute of Training</span>
  </div>
  <div class="abs search">
    <span>Search</span>
    <button aria-label="Search"><svg width="14" height="14" viewBox="0 0 14 14"><circle cx="6" cy="6" r="4.3" fill="none" stroke="#fff" stroke-width="1.8"/><line x1="9.2" y1="9.2" x2="13" y2="13" stroke="#fff" stroke-width="2"/></svg></button>
  </div>
  <div class="abs phone">
    <span class="phone-dot"><svg width="14" height="14" viewBox="0 0 14 14"><path d="M3 1l2.5 3-1.5 1.5c.8 1.8 2.2 3.2 4 4L9.5 8l3 2.5-1.5 2.5C6 12.5 1.5 8 1 2.5z" fill="#fff"/></svg></span>
    <span>+61 8 5550 1234</span>
  </div>
  <div class="abs btn-top" style="top:37px">ENROL NOW</div>
  <div class="abs btn-top" style="top:77px">INFO PACK</div>
</header>

<nav class="section main-nav">
  <ul>
    <li class="active">Home</li>
    <li>About Us</li>
    <li>Courses</li>
    <li>Class Schedule</li>
    <li>Traineeships Queensland Funding</li>
    <li>Blog</li>
    <li>Corporate Training</li>
    <li>Contact us</li>
  </ul>
</nav>

<section class="section hero">
  <div class="abs hero-photo" role="img" aria-label="Photo of two medical professionals in white coats reviewing work at a screen"></div>
  <div class="abs hero-caption">
    <div class="kicker">Medical and Dental</div>
    <h1>Recruitment</h1>
    <p>Nemo enim ipsam voluptatem quia voluptas sit aspernatur aut odit aut fugit.</p>
    <span class="btn">View Details</span>
  </div>
  <div class="abs arrow-round" style="left:64px;top:191px"><svg width="10" height="12" viewBox="0 0 10 12"><path d="M7 1L2 6l5 5" fill="none" stroke="#fff" stroke-width="2"/></svg></div>
  <div class="abs arrow-round" style="left:1096px;top:191px"><svg width="10" height="12" viewBox="0 0 10 12"><path d="M3 1l5 5-5 5" fill="none" stroke="#fff" stroke-width="2"/></svg></div>
  <form class="abs enquire">
    <h2>Enquire Now</h2>
    <div class="field">Name</div>
    <div class="field">Email</div>
    <div class="field">Course</div>
    <div class="field">State</div>
    <div class="field">Mobile</div>
    <div class="submit">SUBMIT</div>
  </form>
</section>

<section class="section courses">
  <svg class="abs band-arrow" style="left:84px" width="14" height="24" viewBox="0 0 14 24"><path d="M12 2L3 12l9 10" fill="none" stroke="#fff" stroke-width="2.5"/></svg>
  <svg class="abs band-arrow" style="left:1092px" width="14" height="24" viewBox="0 0 14 24"><path d="M2 2l9 10-9 10" fill="none" stroke="#fff" stroke-width="2.5"/></svg>
  <div class="abs course" style="left:116px">
    <div class="icon"><svg width="46" height="40" viewBox="0 0 46 40"><rect x="3" y="22" width="40" height="4" fill="#0a5bc4"/><rect x="7" y="26" width="32" height="12" fill="none" stroke="#0a5bc4" stroke-width="2.5"/><circle cx="23" cy="9" r="5" fill="none" stroke="#0a5bc4" stroke-width="2.5"/><path d="M14 22c0-5 4-8 9-8s9 3 9 8" fill="none" stroke="#0a5bc4" stroke-width="2.5"/></svg></div>
    <h3>Medical Reception &amp; Terminology</h3>
    <p>Nemo enim ipsam voluptatem quia voluptas sit aspernatur</p>
  </div>
  <div class="abs course" style="left:371px">
    <div class="icon"><svg width="40" height="42" viewBox="0 0 40 42"><path d="M6 14C6 6 12 2 20 2s14 4 14 12v4H6z" fill="#0a5bc4"/><rect x="17" y="6" width="6" height="10" fill="#fff"/><rect x="15" y="8" width="10" height="6" fill="#fff"/><circle cx="20" cy="24" r="7" fill="#0a5bc4"/><path d="M6 42c0-8 6-11 14-11s14 3 14 11z" fill="#0a5bc4"/></svg></div>
    <h3>Cert III Business Administration</h3>
    <p>Nemo enim ipsam voluptatem quia voluptas sit aspernatur</p>
  </div>
  <div class="abs course" style="left:618px">
    <div class="icon"><svg width="34" height="42" viewBox="0 0 34 42"><rect x="2" y="5" width="30" height="35" rx="2" fill="none" stroke="#0a5bc4" stroke-width="2.5"/><rect x="11" y="2" width="12" height="6" fill="#0a5bc4"/><path d="M8 16h4M15 16h11M8 23h4M15 23h11M8 30h4M15 30h11" stroke="#0a5bc4" stroke-width="2.5"/></svg></div>
    <h3>Medical Terminology</h3>
    <p>Nemo enim ipsam voluptatem quia voluptas sit aspernatur</p>
  </div>
  <div class="abs course" style="left:857px">
    <div class="icon"><svg width="48" height="36" viewBox="0 0 48 36"><path d="M24 2v10" stroke="#0a5bc4" stroke-width="2.5" fill="none"/><rect x="2" y="12" width="44" height="22" rx="3" fill="none" stroke="#0a5bc4" stroke-width="2.5"/><path d="M8 19h3M14 19h3M20 19h3M26 19h3M32 19h3M38 19h3M8 25h3M38 25h3M14 27h20" stroke="#0a5bc4" stroke-width="2.5"/></svg></div>
    <h3>Keyboard and Typing</h3>
    <p>Nemo enim ipsam voluptatem quia voluptas sit aspernatur</p>
  </div>
</section>

<section class="section welcome">
  <h2>Welcome to Harbourlinehealth</h2>
  <p>Harbourline is Australia's Leading Provider of Educational, Training and Support Services for the Medical and Dental industry - enabling students to be immediately skilled and 'Job Ready' for a career in Health. Harbourline is a Registered Training Organisation offering specialised Medical Administration Training in over 15 locations Australia wide. Harbourline have trained thousands of students the required knowledge and skills to become successful health care administrators.</p>
  <span class="btn-small">Read More</span>
</section>

<section class="section testimonials">
  <div class="abs photo" role="img" aria-label="Muted photo of health workers studying together at a desk"></div>
  <h2>Testimonials</h2>
  <p>I want to say a huge thank you for the course and knowledge I came away with. I have secured a fantastic job after my first application! Such good value for money too! I would highly recommend it. I'm a mature age person so it's never too late to up-skill yourself to get what you deserve!</p>
  <div class="who">Mara Quinn</div>
  <div class="t-controls">
    <span><svg width="6" height="10" viewBox="0 0 6 10"><path d="M5 1L1 5l4 4" fill="none" stroke="#fff" stroke-width="1.4"/></svg></span>
    <span><svg width="6" height="10" viewBox="0 0 6 10"><path d="M1 1l4 4-4 4" fill="none" stroke="#fff" stroke-width="1.4"/></svg></span>
  </div>
</section>

<section class="section why">
  <h2>Why Harbourline Institute ?</h2>
  <div class="abs feature" style="left:128px;top:120px">
    <svg width="26" height="26" viewBox="0 0 26 26"><path d="M4 2v8a6 6 0 0012 0V2" fill="none" stroke="#222" stroke-width="2"/><path d="M10 16v3a5 5 0 0010 0v-5" fill="none" stroke="#222" stroke-width="2"/><circle cx="20" cy="12" r="2.5" fill="#222"/></svg>
    <h3>Quality</h3>
    <p>Harbourline delivery quality, effective training facilitated by industry leaders. Just ask our students who rate us on average of 4.7 out of 5.</p>
  </div>
  <div class="abs feature" style="left:637px;top:120px">
    <svg width="26" height="26" viewBox="0 0 26 26"><circle cx="13" cy="7" r="5" fill="#222"/><path d="M3 25c0-7 4-11 10-11s10 4 10 11z" fill="#222"/><rect x="11" y="17" width="4" height="5" fill="#fff"/></svg>
    <h3>Experience</h3>
    <p>Harbourline is Australia's largest and leading providers of nationally recognised training in health administration – training from over 17 locations</p>
  </div>
  <div class="abs feature" style="left:128px;top:216px">
    <svg width="26" height="26" viewBox="0 0 26 26"><rect x="5" y="2" width="16" height="23" fill="none" stroke="#222" stroke-width="2"/><path d="M9 7h3M14 7h3M9 12h3M14 12h3M9 17h3M14 17h3" stroke="#222" stroke-width="2"/><rect x="11" y="20" width="4" height="5" fill="#222"/></svg>
    <h3>Value</h3>
    <p>Harbourline delivery quality, effective training facilitated by industry leaders. Just ask our students who rate us on average of 4.7 out of 5.</p>
  </div>
  <div class="abs feature" style="left:637px;top:216px">
    <svg width="26" height="26" viewBox="0 0 26 26"><path d="M9 2h8M10 2v8L3 23h20L16 10V2" fill="#222" stroke="#222" stroke-width="2" stroke-linejoin="round"/></svg>
    <h3>Industry Recognised</h3>
    <p>Harbourline delivery quality, effective training facilitated by industry leaders. Just ask our students who rate us on average of 4.7 out of 5.</p>
  </div>
  <div class="abs feature" style="left:128px;top:320px">
    <svg width="26" height="26" viewBox="0 0 26 26"><rect x="1" y="7" width="24" height="16" rx="2" fill="#222"/><path d="M9 7V4h8v3" fill="none" stroke="#222" stroke-width="2"/><rect x="11" y="13" width="4" height="3" fill="#fff"/></svg>
    <h3>Great Job Results</h3>
    <p>Harbourline delivery quality, effective training facilitated by industry leaders. Just ask our students who rate us on average of 4.7 out of 5.</p>
  </div>
</section>

<section class="section blog">
  <h2>Recent Blog</h2>
  <article class="abs post" style="left:132px">
    <div class="thumb" role="img" aria-label="Photo of researchers in lab coats working with test tubes" style="background:linear-gradient(120deg,#b9c9d6,#e9edf0 50%,#c2a98f)"></div>
    <h3>Medical Reception Training</h3>
    <div class="date">JUN 20,2015</div>
    <p>Nemo enim ipsam voluptatem quia voluptas sit aspernatur aut odit aut fugit, sed</p>
    <div class="more">READ MORE <svg width="10" height="10" viewBox="0 0 10 10"><circle cx="5" cy="5" r="4.2" fill="none" stroke="#0747a0" stroke-width="1.3"/><path d="M4 3l2 2-2 2" fill="none" stroke="#0747a0" stroke-width="1.3"/></svg></div>
  </article>
  <article class="abs post" style="left:457px">
    <div class="thumb" role="img" aria-label="Photo of a stethoscope on a desk with staff in the background" style="background:linear-gradient(120deg,#9fc3e4,#e6f0f8 55%,#7fa9d2)"></div>
    <h3>Medical Reception Training</h3>
    <div class="date">JUN 20,2015</div>
    <p>Nemo enim ipsam voluptatem quia voluptas sit aspernatur aut odit aut fugit, sed</p>
    <div class="more">READ MORE <svg width="10" height="10" viewBox="0 0 10 10"><circle cx="5" cy="5" r="4.2" fill="none" stroke="#0747a0" stroke-width="1.3"/><path d="M4 3l2 2-2 2" fill="none" stroke="#0747a0" stroke-width="1.3"/></svg></div>
  </article>
  <article class="abs post" style="left:782px">
    <div class="thumb" role="img" aria-label="Photo of a lab technician working among laboratory shelves" style="background:linear-gradient(120deg,#7fa3c9,#d8e4ef 55%,#a9c0d6)"></div>
    <h3>Medical Reception Training</h3>
    <div class="date">JUN 20,2015</div>
    <p>Nemo enim ipsam voluptatem quia voluptas sit aspernatur aut odit aut fugit, sed</p>
    <div class="more">READ MORE <svg width="10" height="10" viewBox="0 0 10 10"><circle cx="5" cy="5" r="4.2" fill="none" stroke="#0747a0" stroke-width="1.3"/><path d="M4 3l2 2-2 2" fill="none" stroke="#0747a0" stroke-width="1.3"/></svg></div>
  </article>
  <div class="abs live-chat"><svg width="18" height="16" viewBox="0 0 18 16"><ellipse cx="8" cy="6" rx="7" ry="5" fill="#fff"/><path d="M3 9l-1 5 5-3z" fill="#fff"/></svg>LIVE CHAT</div>
</section>

<footer class="section site-footer">
  <div class="abs f-brand"><span class="brand-name">Harbourline Institute of Training</span></div>
  <div class="abs socials"><span></span><span></span><span></span></div>
  <div class="abs f-links">
    <h4>Quick Links</h4>
    <ul>
      <li>Home</li><li>About Us</li><li>Recruitment</li><li>Courses</li><li>Class Schedule</li><li>Traineeships Queensland Funding</li>
    </ul>
  </div>
  <div class="abs f-news">
    <h4>Newsletter</h4>
    <p>Subscribe newsletter to receive the latest news</p>
    <div class="input">Enter Your Mail Id</div>
    <span class="sub">Subscribe</span>
  </div>
  <div class="abs f-contact">
    <h4>COntact us</h4>
    <ul>
      <li><svg width="12" height="11" viewBox="0 0 12 11"><path d="M1 3c2-3 8-3 10 0v2H8V3.5H4V5H1z" fill="#eee"/><rect x="2" y="6" width="8" height="5" fill="#eee"/></svg>+61 8 5550 1234</li>
      <li><svg width="12" height="11" viewBox="0 0 12 11"><rect x="3" y="0" width="6" height="3" fill="#eee"/><rect x="0" y="3" width="12" height="5" fill="#eee"/><rect x="3" y="7" width="6" height="4" fill="#eee"/></svg>+61 8 5550 1234</li>
      <li><svg width="12" height="10" viewBox="0 0 12 10"><rect x=".5" y=".5" width="11" height="9" fill="none" stroke="#eee"/><path d="M.5 .5L6 5l5.5-4.5" fill="none" stroke="#eee"/></svg><a>info@harbourline.example</a></li>
      <li><svg width="12" height="14" viewBox="0 0 12 14"><path d="M6 14S1 8 1 5a5 5 0 0110 0c0 3-5 9-5 9z" fill="#eee"/><circle cx="6" cy="5" r="2" fill="#333"/></svg>Riverside House, 40 Acacia Way, Innovation Park, Kelmscott, WA</li>
    </ul>
  </div>
</footer>

<div class="section copyright">2016© harbourlinehealth.com.au. All Right Reserved</div>

</body>
</html>
```